Duct Manufacturing Company new to the industry needs business card and stationary design

we are sheet metal duct manufacturers looking for a business card design to fit my new business logo.
nothing to crazy that will date, but want it to stand out from the crowed.
I'm sure you guys will work it out.

Contact Information for Business Card

Glen Marsh
Director

Address
17 Dorwell St
Tallowmere NSW 2694

0438 760 514

Sales@flowbend.com.au

Font styles to use
Other font styles liked:
• BankGothic md bt

Requirements
Nice to have
• Like the idea of corner rounded to match logo
• like to keep colours flowing
• font I like sharp square not rounded

```html
<!DOCTYPE html>
<html lang="en">
<head>
<meta charset="utf-8">
<title>Flowbend Industries – Business Card</title>
<link rel="stylesheet" href="https://fonts.googleapis.com/css2?family=Michroma&display=swap">
<style>
  :root {
    --page-bg: #e9ebee;
    --blue-deep: #0a6fb8;
    --blue-mid: #1a8fd0;
    --blue-light: #35b3e6;
    --green: #8cc63f;
    --card-white: #ffffff;
    --ink: #1d1d1f;
    --accent-blue: #1a8fd0;
  }
  * { box-sizing: border-box; margin: 0; padding: 0; }
  html, body {
    width: 1200px;
    height: 780px;
    overflow: hidden;
    background: var(--page-bg);
  }
  .stage {
    width: 1200px;
    height: 780px;
    display: flex;
    align-items: center;
    justify-content: center;
  }
  .business-card {
    position: relative;
    width: 910px;
    height: 520px;
    border-radius: 18px;
    overflow: hidden;
    background: var(--card-white);
    box-shadow: 0 14px 40px rgba(0, 0, 0, 0.18);
    font-family: "Michroma", "Arial", sans-serif;
  }
  .card-background {
    position: absolute;
    inset: 0;
    width: 100%;
    height: 100%;
  }
  .card-content {
    position: absolute;
    right: 60px;
    top: 70px;
    width: 580px;
    text-align: right;
  }
  .brand-lockup {
    display: flex;
    align-items: center;
    justify-content: flex-end;
    gap: 22px;
  }
  .brand-mark {
    width: 74px;
    height: 74px;
    border-radius: 50%;
    background: var(--accent-blue);
    flex: none;
  }
  .brand-name {
    color: var(--green);
    font-size: 40px;
    line-height: 1.15;
    letter-spacing: 1px;
    text-transform: uppercase;
    text-align: left;
  }
  .contact-block {
    margin-top: 70px;
    color: var(--ink);
    font-size: 17px;
    line-height: 1.9;
    letter-spacing: 1.5px;
    font-variant: small-caps;
    white-space: nowrap;
  }
  .contact-name {
    color: var(--accent-blue);
    text-transform: uppercase;
    font-size: 20px;
  }
  .contact-label { color: var(--accent-blue); }
  .divider { color: var(--ink); margin: 0 6px; }
</style>
</head>
<body>
  <main class="stage">
    <article class="business-card">
      <svg class="card-background" viewBox="0 0 910 520" preserveAspectRatio="none" aria-hidden="true">
        <defs>
          <linearGradient id="blueField" x1="0" y1="0" x2="1" y2="1">
            <stop offset="0" stop-color="#35b3e6"/>
            <stop offset="0.55" stop-color="#1a8fd0"/>
            <stop offset="1" stop-color="#0a6fb8"/>
          </linearGradient>
        </defs>
        <rect class="blue-field" width="910" height="520" fill="url(#blueField)"/>
        <ellipse class="white-halo" cx="650" cy="250" rx="520" ry="360" fill="#ffffff"/>
        <ellipse class="green-ring" cx="650" cy="250" rx="495" ry="340" fill="#8cc63f"/>
        <ellipse class="white-face" cx="660" cy="248" rx="478" ry="324" fill="#ffffff"/>
      </svg>

      <div class="card-content">
        <div class="brand-lockup">
          <span class="brand-mark"></span>
          <span class="brand-name">Flowbend<br>Industries</span>
        </div>

        <div class="contact-block">
          <p class="contact-role">Director <span class="divider">|</span> <span class="contact-name">Glen Marsh</span></p>
          <p class="contact-line">Sales@flowbend.com.au <span class="contact-label">:E</span> 0438 760 514 <span class="contact-label">:P</span></p>
          <p class="contact-address">17 Dorwell St Tallowmere NSW 2694</p>
        </div>
      </div>
    </article>
  </main>
</body>
</html>
```